Sable Grove products by Voldrin. Beauty, skin care cosmetic products

We are an all natural and organic beauty product company looking for a logo an label design ideas. Our motto is to make products that are safe, natural, in harmony with the earth and that really work. Our products will contribute to the transition from the Old Earth to the Sable Grove (as the image of the two worlds suggests). The earths can be mixed in the label. The label example is a rough sketch.
Updates

The label needs to be 1 (one) inch high and 7 inch long.

Need extra days to review

Target Market(s)

Products made with natural and organic ingredients. Beauty and skin products

Requirements
Must have
• My project must be standing out. We want customers to be draw to he product on the shelf. Wow, this label is different? what is it? All natural? I must try it.
• Must be bold but not outrageous.
• The two earth can be placed on right and left side of the tree of life on the second attachment
Nice to have
• The two Earth can be in the back ground suggesting that this product takes us from chemically and artificially filled products to something new that is in harmony with nature and health.
Should not have
• Should not be boring. Ordinary, easy to forget and ignore patterns, lettering, logos.

```html
<!DOCTYPE html>
<html lang="en">
<head>
<meta charset="utf-8">
<title>Sable Grove – Voldrin Under-Arm-Balm Label</title>
<link rel="stylesheet" href="https://fonts.googleapis.com/css2?family=Sorts+Mill+Goudy&family=Open+Sans:wght@800&family=Montserrat:wght@400;700&display=swap">
<style>
  :root {
    --stage: #000000;
    --navy: #161b2c;
    --deep-blue: #1f3a6e;
    --ocean: #2f6ab8;
    --sky: #5f9be0;
    --leaf: #7fb539;
    --paper: #f2f2f2;
    --ink-light: #dfe6f2;
    --chip: #d9d9d9;
    --code-grey: #555555;
  }
  * { margin: 0; padding: 0; box-sizing: border-box; }
  html, body { width: 1200px; height: 526px; overflow: hidden; background: var(--stage); }
  .label {
    position: absolute; left: 40px; top: 163px; width: 1120px; height: 200px;
    display: grid; grid-template-columns: 370px 380px 370px;
    overflow: hidden;
  }
  .panel { position: relative; overflow: hidden; }
  .panel-art { position: absolute; inset: 0; }
  .panel-back .panel-art { background: radial-gradient(ellipse at 75% 55%, #1e3f5f 0%, var(--deep-blue) 45%, #2d4f8f 100%); }
  .panel-front .panel-art { background: radial-gradient(circle at 50% 45%, #1f2f48 0%, var(--navy) 60%, #23314f 100%); }
  .panel-side .panel-art { background: radial-gradient(ellipse at 30% 70%, var(--navy) 0%, var(--deep-blue) 40%, var(--ocean) 75%, var(--sky) 100%); }
  .content { position: relative; z-index: 1; }

  .panel-back .content {
    padding: 26px 18px 0 20px;
    font-family: "Sorts Mill Goudy", serif; font-size: 10.5px; line-height: 1.3; color: var(--ink-light);
  }
  .panel-back p { margin-bottom: 3px; }
  .panel-back .lead { font-family: "Montserrat", sans-serif; font-weight: 700; font-size: 9px; text-transform: uppercase; }
  .warning { border: 1px solid var(--ink-light); padding: 3px 6px; margin-top: 4px; }

  .panel-front .content { text-align: center; padding-top: 22px; color: var(--paper); }
  .maker { font-family: "Sorts Mill Goudy", serif; font-size: 15px; }
  .claim { font-family: "Sorts Mill Goudy", serif; font-size: 17px; color: var(--leaf); margin-top: 6px; }
  .rule { width: 200px; height: 1px; background: var(--paper); margin: 3px auto 0; }
  .brand { font-family: "Open Sans", sans-serif; font-weight: 800; font-size: 54px; line-height: 1; letter-spacing: 1px; margin-top: 2px; }
  .product { font-family: "Open Sans", sans-serif; font-weight: 800; font-size: 21px; line-height: 1.05; color: var(--leaf); letter-spacing: 1px; }
  .free-from { font-family: "Montserrat", sans-serif; font-size: 12px; line-height: 1.15; letter-spacing: 1px; margin-top: 3px; }
  .free-from strong { font-weight: 700; }

  .panel-side .content {
    display: flex; gap: 14px; padding: 34px 0 0 22px;
    font-family: "Sorts Mill Goudy", serif; color: var(--ink-light);
  }
  .address { font-size: 11.5px; line-height: 1.25; width: 190px; }
  .best-before { margin-top: 8px; background: var(--chip); color: var(--navy); font-size: 10px; padding: 1px 8px; width: 175px; }
  .net-wt { margin-top: 8px; font-size: 10.5px; }
  .marks { display: flex; flex-direction: column; align-items: center; gap: 6px; width: 44px; }
  .social { font-family: "Sorts Mill Goudy", serif; font-size: 8px; color: var(--paper); display: flex; align-items: center; gap: 3px; }
  .social .dot { width: 7px; height: 7px; border-radius: 50%; background: var(--paper); display: inline-block; }
  .code-panel { position: absolute; right: 16px; top: 36px; width: 44px; height: 130px; background: var(--code-grey); z-index: 1; }
</style>
</head>
<body>
<main class="label">
  <section class="panel panel-back">
    <div class="panel-art" role="img" aria-label="Blended globe artwork in deep blue and green tones"></div>
    <div class="content">
      <p><span class="lead">Ingredients:</span> Organic Coconut (Cocos nucifera) Oil, Organic Bees Wax, Shea (Butyrospermum Parkii) Butter, Arrowroot (Mainhot Esculenta) Powder, Magnesium Oil, Nahcolite (Natural Baking Soda)</p>
      <p><span class="lead">Directions:</span> With the finger or spatula apply a pee size product under the arm and spred it on, if applied night after a shave it might sting a bit. Wait a few minutes and the apply.</p>
      <p class="warning"><span class="lead">Warning:</span> External use only. Discontinue use if irritation occurs. Do not apply to open cuts or wounds.</p>
    </div>
  </section>

  <section class="panel panel-front">
    <div class="panel-art" role="img" aria-label="Tree of life between two globes, dark navy background artwork"></div>
    <div class="content">
      <p class="maker">Sable Grove Products by:</p>
      <p class="claim">100% NATURAL INGREDIENTS</p>
      <div class="rule"></div>
      <h1 class="brand">VOLDRIN</h1>
      <p class="product">UNDER-ARM-BALM</p>
      <p class="free-from"><strong>No</strong> Aluminum, <strong>No</strong> Parabens,<br><strong>No</strong> Phthalates</p>
    </div>
  </section>

  <section class="panel panel-side">
    <div class="panel-art" role="img" aria-label="Renewed globe artwork in bright ocean blues"></div>
    <div class="content">
      <div class="address">
        <p>Manufactured by Voldrin LLC<br>0000 Meadow Lane Road, Linden Falls MD 00000<br>Learn more at:<br>Voldrin.example</p>
        <p class="best-before">Best before:</p>
        <p class="net-wt">Net Wt. 2oz (56 g)</p>
      </div>
      <div class="marks">
        <svg width="34" height="30" viewBox="0 0 34 30" aria-hidden="true"><polygon points="17,2 32,28 2,28" fill="none" stroke="#7fb539" stroke-width="2.5"/></svg>
        <svg width="28" height="28" viewBox="0 0 28 28" aria-hidden="true"><circle cx="14" cy="14" r="12" fill="none" stroke="#f2f2f2" stroke-width="1.5"/></svg>
        <p class="social"><span class="dot"></span>@voldrin</p>
      </div>
    </div>
    <div class="code-panel"></div>
  </section>
</main>
</body>
</html>
```